Hardcore nerd needs to stand out in a sea of dull Defence business cards

Wombarra Devices is a new Australian consulting engineering company that turns research and theory into practical systems. No evangelistic fluff, just mathematics and physics into electronic and optical circuits for consumer products, scientific research or Defence applications.

We already have a recognised logo (provided) which is often dark blue/black on a light background but we're open to other combinations. (Us engineers tend to have limited aesthetic imagination :)

Some of our recent products have included:
* Instrumentation for electrical testing,
* Radar jammers,
* GPS antenna design,
* Satellite tracking systems,
* High power lasers

We're open to both single and double-sided designs - happy to be convinced either way.

P.S. Another group is working on the web page, so - alas - our web site is currently of no use for images/ideas...

Target Market(s)

Engineering managers,
Scientists

Contact Information for Business Card

Dr Colin Harte
R&D Engineer

colin@wombarradevices.com.au
0427 563 710

PO Box XXX (to be confirmed)
Kelsby ACT 2917
Australia

Font styles to use
Serif
Sans Serif

Colors

Designer to choose colors to be used in the design.

Requirements
Must have
• My contact details!
• I've had many (great) "bold and plain" designs submitted already, so feel free to be artistically creative :)
• Happy to take advice re fonts/colours/printability etc.
Nice to have
• I'm not sure if "lists" are more at home on a CV than a business card, but representative services include:
• Applied electromagnetics
• RF and high speed electronics
• Signal and image processing
• Electro-optical and laser systems
• Concept-to-prototype design services
• If you're considering double sided cards, then often measuring/alignment grids/rulers feature on the back of similar cards.
• e.g. https://www.veltranoptics.example/newgrouppage9.cfm?objectgroup_id=4183
• https://www.veltranoptics.example/newgrouppage9.cfm?objectgroup_ID=4185
• ..or even a "Smith chart" (google will return lots)
• Generic images to represent a capability might work - googling images associated with keyword for each of these areas might help:
• - "passive radar", "phased array", "fdtd", "vircator"
• RF and high speed electronic design
• - "smith chart", "microstrip circuits", "dimensioned drawing", "electronic schematic"
• - "dft", "iir filter"
• - "optical cavity". "laser energy level diagram"
• Background/watermarked images outlines/wireframes/schematics would probably look OK.
Should not have
• If a list of projects/services is provided, it is important not to make the client feel that this is "all" the company can do. Engineering design is a creative discipline (like graphics :)
• Please, no stock "military" snaps like planes, missiles, etc!

```html
<!DOCTYPE html>
<html lang="en">
<head>
<meta charset="utf-8">
<title>Wombarra Devices – Business Card</title>
<link rel="stylesheet" href="https://fonts.googleapis.com/css2?family=Open+Sans:wght@700&family=Lato:wght@400&family=Arimo:wght@700&display=swap">
<style>
  :root {
    --navy: #0d1f63;
    --ink: #2a2a2a;
    --rule: #c4c4c4;
    --card: #ffffff;
    --backdrop: #d9d9d9;
  }
  * { margin: 0; padding: 0; box-sizing: border-box; }
  html, body { width: 1200px; height: 802px; overflow: hidden; }
  body { background: var(--backdrop); position: relative; font-family: "Lato", sans-serif; }

  .card {
    position: absolute;
    top: 274px;
    width: 443px;
    height: 264px;
    overflow: hidden;
  }
  .card--front { left: 136px; background: var(--card); }
  .card--back { left: 624px; background: var(--navy); }

  .front-band {
    position: absolute; left: 0; right: 0; bottom: 0; height: 8px;
    background: var(--navy);
  }

  .brand-mark {
    position: absolute; left: 176px; top: 44px;
    width: 58px; height: 58px; border-radius: 50%;
    background: var(--navy);
  }
  .brand-name {
    position: absolute; left: 245px; top: 52px;
    font-family: "Open Sans", sans-serif; font-weight: 700;
    color: var(--navy); font-size: 26px; line-height: 1;
  }
  .brand-name span { display: block; }
  .brand-name .line-two { font-size: 15px; letter-spacing: 4.2px; margin-top: 5px; }

  .person-name {
    position: absolute; left: 23px; top: 150px;
    font-family: "Arimo", sans-serif; font-weight: 700;
    font-size: 16px; color: var(--navy); letter-spacing: 0.1px;
  }
  .person-role {
    position: absolute; left: 23px; top: 168px;
    font-size: 12.5px; color: var(--ink);
  }
  .divider {
    position: absolute; left: 112px; top: 175px; width: 290px; height: 1px;
    background: var(--rule);
  }
  .contact {
    position: absolute; left: 23px;
    font-size: 12.5px; color: var(--ink);
    display: flex; align-items: center; gap: 4px;
  }
  .contact svg { width: 10px; height: 10px; fill: var(--navy); flex: none; }
  .contact--phone { top: 190px; }
  .contact--email { top: 206px; }
  .contact--post { top: 231px; }

  .back-name {
    position: absolute; left: 0; right: 0; top: 94px;
    text-align: center; color: #ffffff;
    font-family: "Open Sans", sans-serif; font-weight: 700; line-height: 1;
  }
  .back-name .line-one { display: block; font-size: 40px; letter-spacing: 0.5px; }
  .back-name .line-two { display: block; font-size: 24px; letter-spacing: 6px; margin-top: 6px; }
</style>
</head>
<body>

  <section class="card card--front" aria-label="Card front">
    <div class="brand-mark" aria-hidden="true"></div>
    <div class="brand-name"><span>WOMBARRA</span><span class="line-two">DEVICES</span></div>

    <p class="person-name">DR COLIN HARTE</p>
    <p class="person-role">R&amp;D Engineer</p>
    <div class="divider"></div>

    <p class="contact contact--phone">
      <svg viewBox="0 0 10 10" aria-hidden="true"><path d="M1 4.2C1 2.6 2.6 1.6 5 1.6s4 1 4 2.6v.6H7V3.8H3v1H1zM2.2 5.4h5.6L9 9H1z"/></svg>
      0427 563 710
    </p>
    <p class="contact contact--email">
      <svg viewBox="0 0 10 10" aria-hidden="true"><path d="M0.5 2h9v6h-9z M1.2 2.6 5 5.6 8.8 2.6" /></svg>
      colin@wombarradevices.com.au
    </p>
    <p class="contact contact--post">
      <svg viewBox="0 0 10 10" aria-hidden="true"><path d="M5 0.3C3.1 0.3 1.8 1.7 1.8 3.5 1.8 6 5 9.7 5 9.7S8.2 6 8.2 3.5C8.2 1.7 6.9 0.3 5 0.3zm0 4.6a1.3 1.3 0 1 1 0-2.6 1.3 1.3 0 0 1 0 2.6z"/></svg>
      PO Box XXX&nbsp; Kelsby ACT 2917, Australia
    </p>

    <div class="front-band"></div>
  </section>

  <section class="card card--back" aria-label="Card back">
    <p class="back-name"><span class="line-one">WOMBARRA</span><span class="line-two">DEVICES</span></p>
  </section>

</body>
</html>
```